Onboarding Carousel UI/UX design

We need a great UI/UX design for our onboarding carousel as attached in the PDF document. The chosen designers will be given our brand book with colors and styles to be used. The images must be focused on the content of each slide and be professional unique style (Do not use the childish cartoons we have used for placeholders)

Industry/Entity Type

Mortgage Brokerage

Number of Pages Required

5+ page

Font styles to use
Other font styles liked:
• Roboto

Requirements
Must have
• Great UI / UX design
Very relevant content of the images to match the slide
Nice to have
• Brand book

https://pv.lumorak.com/view/ed991dda-3474-4c3e-9747-882e21ba3df5-b8ca/?fullscreen

Image styles we like. Would need to be customized and made unique for us.

https://pinvarlo.com/shots/6300615-Torvane-Quillet-Illustration-Collaboration
https://meltridgestudio.co.za/software-client-style-frames
Should not have
• Do not use the childish images we have used as placeholders

```html
<!DOCTYPE html>
<html lang="en">
<head>
<meta charset="utf-8">
<title>Onboarding – Apply for the right loan</title>
<link rel="stylesheet" href="https://fonts.googleapis.com/css2?family=Roboto:wght@300;400;700&display=swap">
<style>
  :root {
    --page-bg: #ffffff;
    --screen-bg: #f6f1f0;
    --ink: #111111;
    --muted: #555555;
    --nav-line: #111111;
    --accent: #0ea2e8;
    --art-warm: #f3dcc0;
    --art-cool: #cfe3ef;
    --art-green: #d5e9cf;
  }
  * { box-sizing: border-box; margin: 0; padding: 0; }
  html, body {
    width: 1200px;
    height: 2598px;
    overflow: hidden;
    background: var(--page-bg);
    font-family: "Roboto", Arial, sans-serif;
  }
  .onboarding-screen {
    position: relative;
    width: 1200px;
    height: 2598px;
    background: var(--screen-bg);
    border-radius: 80px;
    overflow: hidden;
  }
  .slide-title {
    position: absolute;
    left: 115px;
    top: 250px;
    font-weight: 700;
    font-size: 82px;
    line-height: 112px;
    color: var(--ink);
    letter-spacing: -0.5px;
  }
  .slide-illustration {
    position: absolute;
    left: 106px;
    top: 680px;
    width: 992px;
    height: 996px;
    border-radius: 50%;
    background: radial-gradient(circle at 50% 45%, var(--art-cool) 0%, var(--art-green) 55%, var(--art-warm) 100%);
  }
  .slide-body {
    position: absolute;
    left: 0;
    right: 0;
    top: 1700px;
    text-align: center;
    font-size: 58px;
    line-height: 77px;
    font-weight: 400;
    color: var(--ink);
  }
  .slide-note {
    position: absolute;
    left: 0;
    right: 0;
    top: 2052px;
    text-align: center;
    font-size: 38px;
    line-height: 54px;
    font-weight: 300;
    color: var(--muted);
  }
  .carousel-nav {
    position: absolute;
    left: 0;
    top: 2340px;
  }
</style>
</head>
<body>
<main class="onboarding-screen">
  <h1 class="slide-title">Apply for the<br>right loan<br>for your needs</h1>

  <div class="slide-illustration" role="img" aria-label="Illustration of a person applying for a loan on a laptop, framed by a ring of coloured circles"></div>

  <p class="slide-body">You will be presented with your<br>options, upload any supporting<br>documents and then submit<br>your application online</p>
  <p class="slide-note">Then we take it from here to get<br>your approval</p>

  <svg class="carousel-nav" width="1200" height="110" viewBox="0 0 1200 110" role="group" aria-label="Slide 6 of 7">
    <g fill="none" stroke="var(--nav-line)" stroke-width="4">
      <circle cx="291" cy="54" r="19"/>
      <circle cx="394" cy="54" r="19"/>
      <circle cx="496" cy="54" r="19"/>
      <circle cx="598" cy="54" r="19"/>
      <circle cx="701" cy="54" r="19"/>
      <circle cx="803" cy="54" r="19" fill="var(--accent)"/>
      <circle cx="906" cy="54" r="19"/>
    </g>
    <g fill="none" stroke="var(--accent)" stroke-width="10" stroke-linecap="round" stroke-linejoin="round" aria-label="Next">
      <polyline points="1008,14 1044,54 1008,94"/>
      <polyline points="1042,14 1078,54 1042,94"/>
    </g>
  </svg>
</main>
</body>
</html>
```